Financial & Tax Strategies

need to get a word press site with existing domains and condense existing content on existing site, make new site dynamic, need mobile too......need to take info from my quorvia website and get modern, relevant site, less verbose on first page, way more things to click and engage people. Would like it to look like this , but with my color scheme and not quite as busy looking. I like much of the content on my tabs. Want maximize by seo capabilities on their as well. The number one thing I can say is to go to my existing website and get content, logo, etc there … www.pinegatelarkgroup.com .

Target Market(s)

Those 40 -65, business owners for at least 5 years. Higher net worth.

Number of Pages Required

5+ page

Font styles to use
Sans Serif

Colors
f04a50
e4daeb
ffffff

Requirements
Must have
• seo maximized, lots of places to click on to contact us, calls to action, relevant, conservative, want it to look like this and have the function as well.....slight variation on messaging, but like the simplicity on first view. https://www.dorrickvale.com/
Nice to have
• Some area along right side where videos we do will be.
Should not have
• feel too busy, but still have lots of opportunities to engage.

```html
<!DOCTYPE html>
<html lang="en">
<head>
<meta charset="utf-8">
<title>Pinegate Lark Group — Tax &amp; Bonus Strategies</title>
<link href="https://fonts.googleapis.com/css2?family=Arimo:wght@400;700&display=swap" rel="stylesheet">
<style>
:root{
  --red:#f04a50;
  --lilac:#e4daeb;
  --lilac-soft:#f3eef6;
  --white:#ffffff;
  --ink:#222222;
  --body:#444444;
  --band:#3a3a3a;
  --footer:#333333;
  --line:#d6cde0;
}
*{box-sizing:border-box;margin:0;padding:0}
html,body{width:1200px;height:3965px;overflow:hidden}
body{font-family:"Arimo",Arial,sans-serif;color:var(--body);background:var(--white);position:relative}
.abs{position:absolute}
a{text-decoration:none}

/* header */
.site-header{position:absolute;left:0;top:0;width:1200px;height:100px;background:var(--white)}
.menu-toggle{left:79px;top:36px;width:24px}
.menu-toggle span{display:block;height:3px;background:#555;margin-bottom:5px}
.brand{left:490px;top:24px;display:flex;align-items:center;gap:12px}
.brand-mark{width:48px;height:48px;border-radius:50%;background:#8a8a8a}
.brand-name{font-size:24px;font-weight:700;line-height:25px;color:#555}
.header-call{left:955px;top:28px;display:flex;gap:10px;align-items:flex-start}
.icon-phone{width:30px;height:30px;border-radius:50%;background:var(--red);display:flex;align-items:center;justify-content:center;flex:0 0 auto}
.header-call p{font-size:12px;line-height:14px;color:#555}
.header-call em{font-style:normal;color:var(--red)}

/* hero */
.hero{left:0;top:100px;width:1200px;height:537px;background:linear-gradient(100deg,#ece8ee 0%,#d6ccd6 35%,#a99aa6 60%,#8d8f9a 85%,#cfc8d2 100%)}
.hero-title{left:270px;top:195px;width:674px;height:139px;background:rgba(40,40,40,.7);display:flex;align-items:center;justify-content:center;text-align:center;color:var(--white);font-size:27px;line-height:37px;font-weight:400}

/* intro */
.intro{left:0;top:637px;width:1200px;height:455px}
.checklist{left:79px;top:47px;width:540px;list-style:none}
.checklist li{display:flex;gap:12px;font-size:13.5px;line-height:16px;color:var(--ink);margin-bottom:18px}
.tick{flex:0 0 16px;height:16px;border:2px solid var(--red);display:flex;align-items:center;justify-content:center}
.intro-copy{left:79px;top:160px;width:540px;font-size:13.5px;line-height:17px;color:var(--body)}
.intro-copy p{margin-bottom:17px}
.intro-photo{left:624px;top:47px;width:499px;height:347px;background:linear-gradient(135deg,#f3eef6,#d9cfdf 50%,#b9b2bd)}

/* contact band */
.contact-band{left:0;top:1092px;width:1200px;height:189px;background:linear-gradient(90deg,#4a4647,#3b393b 50%,#524c52);color:var(--white);text-align:center}
.contact-band h2{position:absolute;left:0;right:0;top:34px;font-size:30px;font-weight:700}
.contact-row{position:absolute;left:0;right:0;top:78px;display:flex;justify-content:center;gap:34px;font-size:32px;font-weight:700}
.contact-row span{display:flex;align-items:center;gap:12px}
.contact-row .icon-phone{width:44px;height:44px}
.contact-band p{position:absolute;left:0;right:0;top:140px;font-size:18px;font-weight:700}

/* feature cards */
.features-area{left:0;top:1281px;width:1200px;height:324px;background:var(--lilac-soft)}
.features{left:79px;top:1323px;width:1044px;display:flex;gap:21px}
.feature{width:245px;height:222px;border-radius:14px;background:var(--white);box-shadow:0 2px 10px rgba(0,0,0,.1);display:flex;flex-direction:column;align-items:center;justify-content:center;text-align:center;padding:0 26px;font-size:14.5px;line-height:18px;color:var(--ink)}
.feature svg{margin-bottom:22px}
.feature.is-active{background:var(--red);color:var(--white)}

/* section bands */
.section-band{left:0;width:1200px;height:60px;background:var(--band);color:var(--white);font-size:30px;font-weight:400;display:flex;align-items:center;justify-content:center}

/* media cards */
.posts{left:74px;top:1716px;width:1063px;display:flex;gap:21px}
.post{width:340px;height:473px;background:var(--white);box-shadow:0 2px 10px rgba(0,0,0,.12);padding:8px 10px}
.post-media{width:100%;height:211px;margin-bottom:14px;position:relative}
.post-media.radio{background:var(--lilac-soft);display:flex;align-items:center;justify-content:center;font-size:34px;font-weight:700;color:var(--red)}
.play{position:absolute;left:50%;top:50%;width:54px;height:54px;margin:-27px 0 0 -27px;border-radius:50%;background:var(--red);display:flex;align-items:center;justify-content:center}
.post h3{font-size:14px;color:var(--ink);margin-bottom:6px}
.post p{font-size:12px;line-height:15.5px;color:#555}
.btn{background:var(--red);color:var(--white);border-radius:22px;font-size:13px;font-weight:700;display:flex;align-items:center;justify-content:center}

/* calculator */
.calculator{left:79px;top:2452px;width:1045px;height:329px;border:1px solid var(--line);background:var(--lilac-soft)}
.calc-row{border-bottom:1px solid var(--line);padding:10px 14px;position:relative}
.calc-row:last-child{border-bottom:0}
.calc-row h4{font-size:26px;font-weight:700;color:#111}
.calc-row p{font-size:22px;color:#222;text-align:center}
.calc-row.summary h4{text-align:center}
.calc-row.summary p{text-align:left;line-height:27px}
.calc-tools{position:absolute;right:12px;top:12px;display:flex;gap:6px;font-size:18px;color:#444}

/* testimonials */
.testimonials-area{left:0;top:2891px;width:1200px;height:450px;background:var(--lilac-soft)}
.testimonials{left:119px;top:2947px;display:flex;gap:31px}
.quote{width:299px;height:342px;background:var(--white);border-radius:14px;box-shadow:0 2px 10px rgba(0,0,0,.1);text-align:center;padding:38px 22px 0}
.avatar{width:80px;height:80px;border-radius:50%;margin:0 auto 22px;background:linear-gradient(var(--lilac),#9a93a4)}
.quote h5{font-size:15px;font-weight:400;color:var(--ink);margin-bottom:14px}
.quote p{font-size:12px;line-height:15.5px;color:#555}
.dots{left:585px;top:3308px;display:flex;gap:6px}
.dots i{width:7px;height:7px;border-radius:50%;background:var(--red)}

/* signup */
.signup-input{left:304px;top:3389px;width:410px;height:37px;border-bottom:1px solid var(--line);font-size:12px;color:#666;padding:12px 8px}
.call-us{left:0;top:3466px;width:1200px;display:flex;justify-content:center;align-items:center;gap:16px;font-size:28px;font-weight:700;color:var(--ink)}
.call-us .icon-phone{width:50px;height:50px}

/* footer */
.site-footer{left:0;top:3570px;width:1200px;height:315px;background:var(--footer);color:#ddd}
.footer-brand{left:79px;top:40px;width:280px}
.footer-brand .brand-line{display:flex;align-items:center;gap:10px;font-size:21px;font-weight:700;color:var(--white);line-height:22px;margin-bottom:16px}
.footer-brand .brand-mark{width:40px;height:40px;background:var(--lilac)}
.footer-brand p{font-size:12px;line-height:15px}
.footer-col h6{font-size:14px;font-weight:400;color:var(--white);padding-bottom:5px;border-bottom:2px solid var(--red);display:inline-block;margin-bottom:14px}
.footer-col ul{list-style:disc;padding-left:16px;font-size:12px;line-height:16px}
.footer-col .addr{font-size:12px;line-height:19px}
.footer-col .addr div{display:flex;gap:7px;align-items:flex-start}
.mini-pin{width:8px;height:8px;border-radius:50%;background:var(--red);margin-top:5px;flex:0 0 8px}
.contact-form{display:grid;grid-template-columns:1fr 1fr 1fr;gap:7px;width:300px}
.field{background:#4a4a4a;height:26px;font-size:11px;color:#ddd;padding:7px 8px}
.field.msg{grid-column:1/4;height:74px}
.footer-btn{width:178px;height:30px;margin-top:8px;border-radius:16px;font-size:12px}

.copyright{left:79px;top:3918px;font-size:12px;color:#555}
.socials{left:935px;top:3913px;display:flex;gap:9px}
.socials i{width:24px;height:24px;border-radius:50%;background:var(--ink)}
.socials i:first-child{background:var(--red)}
</style>
</head>
<body>

<header class="site-header">
  <div class="abs menu-toggle"><span></span><span></span><span></span></div>
  <div class="abs brand"><div class="brand-mark"></div><div class="brand-name">Pinegate<br>Lark Group</div></div>
  <div class="abs header-call">
    <div class="icon-phone"><svg width="16" height="16" viewBox="0 0 24 24"><path fill="#fff" d="M6.6 10.8a15 15 0 0 0 6.6 6.6l2.2-2.2c.3-.3.7-.4 1-.2 1.1.4 2.3.6 3.6.6.6 0 1 .4 1 1V20c0 .6-.4 1-1 1A17 17 0 0 1 3 4c0-.6.4-1 1-1h3.5c.6 0 1 .4 1 1 0 1.3.2 2.5.6 3.6.1.3 0 .7-.2 1z"/></svg></div>
    <p>Confidential Financial<br>Review <em>Call Now</em><br>555.210.4470</p>
  </div>
</header>

<section class="abs hero" role="img" aria-label="Photo of a retired couple reviewing finances together on a sofa">
  <h1 class="abs hero-title">Business Owners &amp; Executives Love Our<br>Tax &amp; Bonus Strategies!</h1>
</section>

<section class="abs intro">
  <ul class="abs checklist">
    <li><span class="tick"><svg width="10" height="10" viewBox="0 0 10 10"><path d="M1 5l3 3 5-7" stroke="#f04a50" stroke-width="2" fill="none"/></svg></span>Executive Bonus Plans &amp; Creative Tax Strategies For Business Owners &amp; Executives</li>
    <li><span class="tick"><svg width="10" height="10" viewBox="0 0 10 10"><path d="M1 5l3 3 5-7" stroke="#f04a50" stroke-width="2" fill="none"/></svg></span>We Can Do What Accountants Can't</li>
  </ul>
  <div class="abs intro-copy">
    <p>Like most business owners, it can be frustrating to hear the same, old remedies from your accountants year after year….. hit rewind and hear the same old pitch, right? Have you ever wondered if there had to be other tax strategies other than buying more vehicles, expanding/buying another business or buying new equipment? There is……that's Pinegate Lark Group.</p>
    <p>Perhaps you want to take your winnings when the economy is good and get out while the going is good? Being forced by the tax code to continually build and reinvest limits opportunities to reap profits. Pinegate Lark Group is unique in that we have access to the most markets that are all top rated and best in class.</p>
    <p>Give us a call at 555.210.4470 or email us at Sales@PinegateLark.com for a one hour look at what Winning the tax game really looks like.</p>
  </div>
  <div class="abs intro-photo" role="img" aria-label="Photo of a smiling senior couple looking at a laptop"></div>
</section>

<section class="abs contact-band">
  <h2>Contact us at</h2>
  <div class="contact-row">
    <span><span class="icon-phone"><svg width="20" height="20" viewBox="0 0 24 24"><path fill="#fff" d="M3 6h18v12H3z"/><path d="M3 6l9 7 9-7" stroke="#f04a50" stroke-width="2" fill="none"/></svg></span>Sales@PinegateLark.com</span>
    <span><span class="icon-phone"><svg width="22" height="22" viewBox="0 0 24 24"><path fill="#fff" d="M6.6 10.8a15 15 0 0 0 6.6 6.6l2.2-2.2c.3-.3.7-.4 1-.2 1.1.4 2.3.6 3.6.6.6 0 1 .4 1 1V20c0 .6-.4 1-1 1A17 17 0 0 1 3 4c0-.6.4-1 1-1h3.5c.6 0 1 .4 1 1 0 1.3.2 2.5.6 3.6.1.3 0 .7-.2 1z"/></svg></span>555.210.4470</span>
  </div>
  <p>For a One Hour Look at What Winning the Tax Game Really Looks Like.</p>
</section>

<div class="abs features-area"></div>
<div class="abs features">
  <a class="feature"><svg width="44" height="44" viewBox="0 0 44 44" fill="none" stroke="#f04a50" stroke-width="2"><path d="M4 40h36M9 40V24h6v16M19 40V14h6v26M29 40V20h6v20"/><path d="M6 14l10-8 8 5 12-8"/></svg>Insuring Portfolios Against Market Crashes</a>
  <a class="feature"><svg width="44" height="44" viewBox="0 0 44 44" fill="none" stroke="#f04a50" stroke-width="2"><path d="M12 6h18v16H12zM10 22h24v6H10zM14 28l-4 12M30 28l4 12M6 40h12M28 40h12"/></svg>Seemingly Small Fees Devastate Retirements.</a>
  <a class="feature is-active"><svg width="44" height="44" viewBox="0 0 44 44" fill="none" stroke="#fff" stroke-width="2"><rect x="4" y="8" width="36" height="28"/><path d="M4 16h36M10 22h10M10 28h10M26 22h8v6h-8z"/></svg>Business Owners &amp; Executives Love Our Tax &amp; Bonus Strategies!</a>
  <a class="feature"><svg width="44" height="44" viewBox="0 0 44 44" fill="none" stroke="#f04a50" stroke-width="2"><path d="M22 22V10M22 14c-6 0-8-4-8-8 6 0 8 4 8 8zM22 18c6 0 8-4 8-8-6 0-8 4-8 8zM12 22h20l-3 18H15z"/></svg>401K, Mutual Fund &amp; IRA Myths Revealed</a>
</div>

<h2 class="abs section-band" style="top:1605px">Blogs, Videos &amp; Radio</h2>

<div class="abs posts">
  <article class="post">
    <div class="post-media radio">Riverline Radio</div>
    <h3>Riverline Radio</h3>
    <p>Catch us on Riverline Radio's Dana Merrow Show Now on KWLN 1490 AM &amp; 97.3 FM. Catch us every Sunday morning on KWLN 1490 AM @ 7 AM.<br>Money Making Pinegate Lark Group's Steady Sam &amp; Regular Ray will make your Sunday morning and financial future yodel</p>
  </article>
  <article class="post">
    <div class="post-media" role="img" aria-label="Photo of a man surrounded by falling banknotes" style="background:linear-gradient(135deg,#eeeaf0,#c7bfcc 50%,#9a95a0)"></div>
    <h3>Money Blog</h3>
    <p>Ever start to think that portfolio and investing is so confusing that you need a financial advisor to help them to your money? Maybe it's by design. Get educated on our blog. Time to get in touch, stay in touch and get educated about your money. Your education is our advantage. Check out our extremely educational and entertaining Money Series with Steady Sam and Regular Ray.</p>
  </article>
  <article class="post">
    <div class="post-media" role="img" aria-label="Video thumbnail with an advisor portrait" style="background:linear-gradient(135deg,#d9cfdf,#a898b0 50%,#e4daeb)"><span class="play"><svg width="20" height="20" viewBox="0 0 20 20"><path d="M6 3l11 7-11 7z" fill="#fff"/></svg></span></div>
    <h3>PLG Videos</h3>
    <p>Here you can find quick videos expanding on some of our strategies, philosophies &amp; products. We are currently under construction. Please come back and visit us in a week.</p>
  </article>
</div>

<a class="abs btn" style="left:502px;top:2255px;width:204px;height:42px">401k Facts</a>

<h2 class="abs section-band" style="top:2347px">Retirement Calculators</h2>

<section class="abs calculator">
  <div class="calc-row"><h4>Retirement plan inputs:</h4><p>Retire at age 67 with 90% of current income</p><span class="calc-tools">✎ [+]</span></div>
  <div class="calc-row"><h4>Investment returns, inflation and Social Security:</h4><p>7% pre-retirement, 4% in retirement, 2.9% inflation, Include Social Security? No</p><span class="calc-tools">✎ [+]</span></div>
  <div class="calc-row summary"><h4>Retirement savings runs out at age 76.</h4><p>Your plan provides $624,048 when you retire. This assumes annual retirement expenses of $68,205 which is 90% of your last year's income of $75,783. This includes $0 per year from Social Security.</p><span class="calc-tools">▮ [+]</span></div>
</section>

<h2 class="abs section-band" style="top:2831px">Testimonials</h2>

<div class="abs testimonials-area"></div>
<div class="abs testimonials">
  <div class="quote"><div class="avatar" role="img" aria-label="Client portrait"></div><h5>Alan Brewer</h5><p>National Enterprise Council Turnaround CEO of the Year<br>I'm a CFO by trade. PLG has strategies for families, executive &amp; business owners that accountants and financial advisors don't have. Highest recommendation</p></div>
  <div class="quote"><div class="avatar" role="img" aria-label="Client portrait"></div><h5>Mark Tolliver</h5><p>Probate Attorney. As an attorney, my job is to weigh risk. As an investor, weighing risk and reward is even more important. As someone retiring in next 15 years, I wanted to eliminate the risks of a stock market crash. PLG does this better than any other company.</p></div>
  <div class="quote"><div class="avatar" role="img" aria-label="Client portrait"></div><h5>Owen Hartley</h5><p>Doctor. Being a doctor requires attention to detail. Pinegate Lark Group helped navigate and educate me on exactly how to decipher my portfolio statement. It would have changed 10 years ago if I would have known what I know now about money. Call them; you'll be happy you did</p></div>
</div>
<div class="abs dots"><i></i><i></i><i></i></div>

<div class="abs signup-input">Shoot us a quick email here</div>
<a class="abs btn" style="left:740px;top:3389px;width:159px;height:37px">Submit</a>

<div class="abs call-us">CALL US <span class="icon-phone"><svg width="24" height="24" viewBox="0 0 24 24"><path fill="#fff" d="M6.6 10.8a15 15 0 0 0 6.6 6.6l2.2-2.2c.3-.3.7-.4 1-.2 1.1.4 2.3.6 3.6.6.6 0 1 .4 1 1V20c0 .6-.4 1-1 1A17 17 0 0 1 3 4c0-.6.4-1 1-1h3.5c.6 0 1 .4 1 1 0 1.3.2 2.5.6 3.6.1.3 0 .7-.2 1z"/></svg></span> 555.210.4470</div>

<footer class="abs site-footer">
  <div class="abs footer-brand">
    <div class="brand-line"><span class="brand-mark"></span>Pinegate<br>Lark Group</div>
    <p>Bringing sensibility, predictability and peace of mind in retirement. We will do things for your financial lives accountants and financial advisors won't and can't.</p>
  </div>
  <div class="abs footer-col" style="left:405px;top:40px">
    <h6>Quick Link</h6>
    <ul><li>Home</li><li>Insuring Portfolios</li><li>Small Fees</li><li>Business Owners</li><li>401K</li><li>Services</li><li>Contact us</li></ul>
  </div>
  <div class="abs footer-col" style="left:571px;top:40px">
    <h6>Address</h6>
    <div class="addr">
      <div><span class="mini-pin"></span><span>4821 Harlow Road,<br>Alder Springs,<br>CA 95000</span></div>
      <div><span class="mini-pin"></span>555.210.4470</div>
      <div><span class="mini-pin"></span>Sales@PinegateLark.com</div>
    </div>
  </div>
  <div class="abs footer-col" style="left:824px;top:40px">
    <h6>Contact us</h6>
    <div class="contact-form">
      <div class="field">Name</div><div class="field">Email</div><div class="field">Phone</div>
      <div class="field msg">Message</div>
    </div>
    <a class="btn footer-btn">Baby Boomer Edition</a>
  </div>
</footer>

<p class="abs copyright">CopyRight © 2019 Pinegate Lark Group. All Right Reserve</p>
<div class="abs socials"><i></i><i></i><i></i><i></i><i></i></div>

</body>
</html>
```